We need an infographic fo a foundation based in Vancouver, BC, Canada.
We need it to be bold and colourful and show what we've done as a foundation over the last year.
Here is the content needed to put into the infographic:
BRIGHT HARBOR FOUNDATION
INFOGRAPHIC
www.brightharbor-example.org
Top section
Image: Map of the world
Text: Where Bright Harbor Foundation is Investing
(see image here for where to pins on the map of the world) http://www.brightharbor-example.org/about/about.aspx?page=2
Next section
What is the Bright Harbor Foundation Providing for Missionaries?
Image: Video camera
Text in video camera image: 82
82 Video Cameras Shipped Overseas
Image: Web Page
Text in web page: 116
116 Web Pages Created
Image: Dollar Bill
Text in Dollar Bill: $6,000
$6,000 in Matching Funds
Image: E-Mail
Text in E-Mail: 67
67 Fundraising Training E-Letters Sent
Missionaries Telling their Story
Image: Vidstream Video
Text: 110
110 Videos Uploaded from the Field
Image: Cell phone
Text 214
214 Text Messages Sent from the Field
Image: Poloroid photo
Text: 580
580 Photos Uploaded from the Field
Funds were raised
In MASSIVE text: $331,291.55
smaller text: Raised for Missionaries and Wired Overseas
Through various ways
Image: beer glass
Text: 1
1 Champion Who Gave Up Beer to Raise Money for Missions
Image: Wedding Cake Topper
Text: 1
1 Champion Who Gave Up their Wedding to Raise Money for Missions
Image: Birthday Present
Text: 1
1 Champion who Gave up Their Birthday to Raise Money for Missions
Image: People
Text 83
83 People Who Have Fundraised for a Missionary
*Stats are up to date as of Nov, 2012
Our website: www.brightharbor-example.org
Target Market(s)
18-60 year olds who have given to the foundation
Industry/Entity Type
Camera

```html
<!DOCTYPE html>
<html lang="en">
<head>
<meta charset="utf-8">
<title>Bright Harbor Foundation Infographic</title>
<link href="https://fonts.googleapis.com/css2?family=Arimo:wght@400;700&display=swap" rel="stylesheet">
<style>
  :root {
    --bg-deep: #0c3546;
    --bg-mid: #15526a;
    --panel: #1d6580;
    --panel-edge: #3a8aa5;
    --heading-bar: #0f4458;
    --white: #ffffff;
    --text-soft: #d6eef6;
    --orange: #f28a1e;
    --grey: #cfd3d6;
    --yellow: #f6c91a;
    --red: #e0342b;
    --green: #7cc242;
    --map-land: #2d7a95;
    --pin: #f28a1e;
  }
  * { margin: 0; padding: 0; box-sizing: border-box; }
  html, body { width: 1200px; height: 2989px; overflow: hidden; }
  body {
    font-family: "Arimo", Arial, sans-serif;
    color: var(--white);
    background: radial-gradient(ellipse at 50% 30%, var(--bg-mid) 0%, var(--bg-deep) 70%);
    position: relative;
  }
  .abs { position: absolute; }

  .header-title { left: 0; width: 1200px; top: 34px; text-align: center; font-size: 48px; font-weight: 700; letter-spacing: 1px; }
  .header-url { left: 0; width: 1200px; top: 98px; text-align: center; font-size: 28px; font-weight: 700; }
  .brand-mark { right: 40px; top: 150px; font-size: 26px; font-weight: 700; display: flex; align-items: center; gap: 10px; }
  .brand-mark .dot { width: 18px; height: 18px; background: var(--white); border-radius: 50%; }

  .world-map { left: 110px; top: 200px; width: 900px; height: 520px; border-radius: 30px;
    background: radial-gradient(ellipse at 50% 50%, var(--map-land) 0%, rgba(45,122,149,0.3) 70%, transparent 100%); }
  .map-caption { left: 0; width: 1200px; top: 752px; text-align: center; font-size: 22px; color: var(--text-soft); }

  .panel { left: 34px; width: 1132px; background: var(--panel); border: 3px solid var(--panel-edge); border-radius: 10px; }
  .panel-heading { position: absolute; left: 20px; right: 20px; top: 20px; height: 60px; background: var(--heading-bar);
    border-radius: 6px; font-size: 34px; font-weight: 700; text-align: center; line-height: 60px; }

  .stat { position: absolute; width: 160px; text-align: center; }
  .stat-icon { width: 128px; height: 128px; margin: 0 auto; border-radius: 16px; display: flex; align-items: center; justify-content: center;
    box-shadow: 0 4px 0 rgba(0,0,0,0.25); }
  .stat-icon .num { background: var(--white); color: #333; font-weight: 700; font-size: 36px; padding: 8px 10px; border-radius: 6px; min-width: 80px; }
  .stat-label { margin-top: 16px; font-size: 20px; line-height: 1.3; color: var(--white); }

  .icon-orange { background: var(--orange); }
  .icon-grey { background: var(--grey); }
  .icon-yellow { background: var(--yellow); }
  .icon-red { background: var(--red); }
  .icon-green { background: var(--green); }
  .icon-white { background: var(--white); }
  .icon-white .num { background: transparent; }

  .kid { position: absolute; border-radius: 40px; }
  .kid-warm { background: linear-gradient(180deg, #f3b77a 0%, #e36d2a 100%); }
  .kid-cool { background: linear-gradient(180deg, #f6d36b 0%, #3ea3c9 100%); }

  .funds-heading { left: 0; width: 1200px; top: 1760px; text-align: center; font-size: 38px; font-weight: 700; }
  .funds-amount { left: 300px; top: 1820px; font-size: 120px; font-weight: 700; letter-spacing: -1px; }
  .funds-note { left: 300px; top: 1970px; width: 820px; text-align: center; font-size: 34px; font-weight: 700; }
  .funds-chart { left: 110px; top: 1840px; }

  .footnote { left: 0; width: 1200px; top: 2605px; text-align: center; font-size: 18px; font-style: normal; color: var(--text-soft); }
  .kids-row { left: 30px; top: 2650px; width: 1140px; height: 250px; border-radius: 60px 60px 0 0;
    background: linear-gradient(90deg, #f28a1e, #f6c91a, #7cc242, #3ea3c9, #e0342b); }
  .footer-url { left: 0; width: 1200px; top: 2925px; text-align: center; font-size: 30px; font-weight: 700; }
</style>
</head>
<body>

<header>
  <div class="abs header-title">BRIGHT HARBOR FOUNDATION</div>
  <div class="abs header-url">www.brightharbor-example.org</div>
  <div class="abs brand-mark"><span class="dot"></span>Bright Harbor</div>
</header>

<section class="map-section">
  <div class="abs world-map" role="img" aria-label="World map with orange pins marking countries where the foundation invests"></div>
  <div class="abs map-caption">Where Bright Harbor Foundation is Investing</div>
</section>

<section class="abs panel" style="top:830px;height:460px;">
  <div class="panel-heading">What is the Bright Harbor Foundation Providing for Missionaries?</div>
  <div class="stat" style="left:90px;top:120px;">
    <div class="stat-icon icon-orange"><span class="num">82</span></div>
    <div class="stat-label">82 Video Cameras Shipped Overseas</div>
  </div>
  <div class="stat" style="left:270px;top:120px;">
    <div class="stat-icon icon-grey"><span class="num">116</span></div>
    <div class="stat-label">116 Web Pages Created</div>
  </div>
  <div class="stat" style="left:450px;top:120px;">
    <div class="stat-icon icon-yellow"><span class="num">$6000</span></div>
    <div class="stat-label">$6,000 in Matching Funds</div>
  </div>
  <div class="stat" style="left:630px;top:120px;">
    <div class="stat-icon icon-red"><span class="num">67</span></div>
    <div class="stat-label">67 Fundraising Training E-Letters Sent</div>
  </div>
  <div class="kid kid-warm" style="left:830px;top:100px;width:240px;height:340px;" role="img" aria-label="Cartoon child waving"></div>
</section>

<section class="abs panel" style="top:1315px;height:410px;">
  <div class="panel-heading">Missionaries Telling their Story</div>
  <div class="kid kid-cool" style="left:40px;top:100px;width:220px;height:290px;" role="img" aria-label="Cartoon child pointing"></div>
  <div class="stat" style="left:300px;top:110px;">
    <div class="stat-icon icon-white"><span class="num">110</span></div>
    <div class="stat-label">110 Videos Uploaded from the Field</div>
  </div>
  <div class="stat" style="left:480px;top:110px;">
    <div class="stat-icon icon-yellow"><span class="num">214</span></div>
    <div class="stat-label">214 Text Messages Sent from the Field</div>
  </div>
  <div class="stat" style="left:660px;top:110px;">
    <div class="stat-icon icon-red"><span class="num">580</span></div>
    <div class="stat-label">580 Photos Uploaded from the Field</div>
  </div>
  <div class="kid kid-warm" style="left:860px;top:100px;width:220px;height:290px;" role="img" aria-label="Cartoon child cheering"></div>
</section>

<section class="funds">
  <div class="abs funds-heading">Funds were raised</div>
  <svg class="abs funds-chart" width="170" height="150" viewBox="0 0 170 150" aria-hidden="true">
    <rect x="10" y="100" width="22" height="45" fill="#ffffff" opacity="0.5"/>
    <rect x="45" y="80" width="22" height="65" fill="#ffffff" opacity="0.5"/>
    <rect x="80" y="60" width="22" height="85" fill="#ffffff" opacity="0.5"/>
    <rect x="115" y="40" width="22" height="105" fill="#ffffff" opacity="0.5"/>
    <polyline points="5,110 55,70 85,85 150,20" fill="none" stroke="#ffffff" stroke-width="10" stroke-linejoin="round"/>
    <polygon points="130,12 165,5 158,40" fill="#ffffff"/>
  </svg>
  <div class="abs funds-amount">$331,291.55</div>
  <div class="abs funds-note">Raised for Missionaries and Wired Overseas</div>
</section>

<section class="abs panel" style="top:2160px;height:430px;">
  <div class="panel-heading">What is the Bright Harbor Foundation Providing for Missionaries?</div>
  <div class="kid kid-warm" style="left:30px;top:100px;width:210px;height:310px;" role="img" aria-label="Cartoon child with backpack"></div>
  <div class="stat" style="left:260px;top:110px;width:200px;">
    <div class="stat-icon icon-orange"><span class="num">1</span></div>
    <div class="stat-label">1 Champion Who Gave Up Beer to Raise Money for Missions</div>
  </div>
  <div class="stat" style="left:470px;top:110px;width:200px;">
    <div class="stat-icon icon-green"><span class="num">1</span></div>
    <div class="stat-label">1 Champion Who Gave Up their Wedding to Raise Money for Missions</div>
  </div>
  <div class="stat" style="left:680px;top:110px;width:200px;">
    <div class="stat-icon icon-yellow"><span class="num">1</span></div>
    <div class="stat-label">1 Champion Who Gave up Their Birthday to Raise Money for Missions</div>
  </div>
  <div class="stat" style="left:890px;top:110px;width:200px;">
    <div class="stat-icon icon-red"><span class="num">83</span></div>
    <div class="stat-label">83 People Who Have Fundraised for a Missionary</div>
  </div>
</section>

<div class="abs footnote">*Stats are up to date as of Nov, 2012</div>
<div class="abs kids-row" role="img" aria-label="Row of cheerful cartoon children in colourful clothes"></div>
<footer class="abs footer-url">www.brightharbor-example.org</footer>

</body>
</html>
```